Indian Lunch Delivery company needs a google ad banner for advertising its offering

We are a Kolkata, India based startup delivering lunch to office buildings in the city. We only serve set meals (vegetarian and non-vegetarian). Minimum order quantity is 5 boxes. The name of the brand is Ruvamesa (Thali=platter). Our USP-
We cook fresh
Trans-fat free
No emulsifiers, preservatives or artificial colorings used.
Importantly, we are a value for money brand. To be precise our meals costs just .99 c.
Target Market(s)
Young professionals
Industry/Entity Type
It Company
Font styles to use
Sans Serif
Requirements
Must have
- Home made food feel to it
Nice to have
- Lots of colours

```html
<!DOCTYPE html>
<html lang="en">
<head>
<meta charset="utf-8">
<title>Ruvamesa – Everyday Healthy</title>
<link rel="stylesheet" href="https://fonts.googleapis.com/css2?family=Roboto:wght@300;400;500;700&display=swap">
<style>
  :root {
    --white: #ffffff;
    --logo-grey: #8e8e8e;
    --coral: #f0897a;
    --food-dark: #3a2418;
    --food-mid: #8a4a22;
    --food-warm: #c07a3a;
  }
  html, body {
    margin: 0;
    padding: 0;
    overflow: hidden;
    background: var(--white);
  }
  .banner {
    position: relative;
    width: 1200px;
    height: 232px;
    overflow: hidden;
    font-family: "Roboto", Arial, sans-serif;
    background: var(--white);
  }
  .banner__food {
    position: absolute;
    inset: 0;
    background:
      radial-gradient(ellipse at 45% 30%, rgba(192,122,58,0.55), transparent 60%),
      radial-gradient(ellipse at 70% 80%, rgba(160,90,40,0.5), transparent 55%),
      linear-gradient(100deg, var(--food-dark) 0%, var(--food-mid) 45%, var(--food-warm) 70%, var(--food-dark) 100%);
  }
  .banner__shapes {
    position: absolute;
    inset: 0;
  }
  .brand {
    position: absolute;
    left: 63px;
    top: 44px;
    width: 144px;
    height: 144px;
    border-radius: 50%;
    background: var(--logo-grey);
    display: flex;
    align-items: center;
    justify-content: center;
  }
  .brand__name {
    color: var(--white);
    font-weight: 700;
    font-size: 19px;
    letter-spacing: 0.5px;
    text-transform: uppercase;
  }
  .tagline {
    position: absolute;
    left: 600px;
    top: 4px;
    width: 170px;
    margin-left: -85px;
    text-align: center;
    color: var(--white);
  }
  .tagline__title {
    margin: 34px 0 0;
    font-weight: 300;
    font-size: 22px;
    line-height: 26px;
  }
  .tagline__sub {
    margin: 14px auto 0;
    width: 128px;
    padding-top: 6px;
    border-top: 1.5px solid var(--white);
    border-bottom: 1.5px solid var(--white);
    padding-bottom: 6px;
    font-weight: 700;
    font-size: 11px;
    line-height: 16px;
    letter-spacing: 0.2px;
  }
  .cta {
    position: absolute;
    left: 948px;
    top: 66px;
    width: 194px;
    height: 40px;
    box-sizing: border-box;
    border: 2px solid var(--white);
    border-radius: 9px;
    color: var(--white);
    font-weight: 500;
    font-size: 16px;
    display: flex;
    align-items: center;
    justify-content: center;
    letter-spacing: 0.3px;
  }
  .website {
    position: absolute;
    left: 948px;
    top: 112px;
    width: 194px;
    text-align: center;
    color: var(--white);
    font-weight: 700;
    font-size: 15px;
    letter-spacing: 0.2px;
  }
</style>
</head>
<body>
<div class="banner">
  <div class="banner__food" role="img" aria-label="Overhead view of a thali platter with bowls of curries, vegetables, rice and flatbreads"></div>

  <svg class="banner__shapes" width="1200" height="232" viewBox="0 0 1200 232" aria-hidden="true">
    <polygon points="0,0 271,0 348,116 271,232 0,232" fill="var(--white)"/>
    <polygon points="929,0 1200,0 1200,232 929,232 845,116" fill="var(--coral)"/>
    <polygon points="600,8 672,49 672,131 600,172 528,131 528,49" fill="rgba(0,0,0,0.15)" stroke="var(--white)" stroke-width="2"/>
  </svg>

  <div class="brand">
    <span class="brand__name">Ruvamesa</span>
  </div>

  <div class="tagline">
    <p class="tagline__title">Everyday<br>Healthy</p>
    <p class="tagline__sub">RECIPES FOR SIMPLE<br>&amp; HEALTHY EATING</p>
  </div>

  <div class="cta">MORE INFO &gt;</div>
  <div class="website">www.ruvamesa.com</div>
</div>
</body>
</html>
```